Retail Package for Ammunition Company

We are looking for a packaging design for a retail boxed ammunition. The "look". Attached will be the logo to be used. The logo is attached and a can be manipulated on the box. Box to represent strength and accuracy. Will need to provide .psd files to allow in house personnel to add/remove text to other calibers and warnings. Wow me with your designs!

Browse Other Brands: http://www.brightfalconsupply.com/brands

The packaging needs to include:
Logo- provided and the following text:

FRONT 1. 9mm 115gr FMJ

BACK 2. WARNING: To avoid serious injury: (1) use only ammunition in good condition; use only in modern firearms in good condition marked for .22 Long Rifle (LR) cartridges; (2) always be sure barrel is free of any obstructions; the barrel should be checked in case of light recoil, or an unusually loud or weak sound heard during firing; (3) wear eye and ear protection; (4) if gun fails to fire, avoid exposure to breech when unloading and point muzzle in a safe direction. Keep firearm pointed in safe direction at all times; (5) discharge may occur if rim is struck; handle with caution, do not drop. (6) Do not shoot at hard surfaces or water to prevent ricochet; (7) Bullet is capable of traveling extreme distances. Know your backstop; (8) Store in cool dry place

3. LEAD WARNING: Discharging firearms in poorly ventilated areas, cleaning firearms, or handling ammunition may result in exposure to lead and other substances known to cause birth defects, reproductive harm, and other serious physical injury. Have adequate ventilation at all times. Wash hands thoroughly after exposure.

Dimensions ; (LxWxH): 5.25" x 2.625" x 1.125"

Target Market(s)

Ammunition Industry

```html
<!DOCTYPE html>
<html lang="en">
<head>
<meta charset="utf-8">
<title>Iron Crest Armory – 9mm 115gr FMJ Box Panels</title>
<link href="https://fonts.googleapis.com/css2?family=Montserrat:wght@600;700;800;900&display=swap" rel="stylesheet">
<style>
  :root {
    --stage: #ffffff;
    --black: #161616;
    --black-soft: #2c2c2c;
    --red-deep: #6e0b0c;
    --red: #9a1a16;
    --red-bright: #a8221b;
    --emblem-tint: rgba(190, 60, 40, 0.28);
    --side-white: #e9e9e9;
    --side-emblem: #8a1a1c;
    --gold-light: #f2dfa0;
    --gold: #d6b566;
    --gold-dark: #a8843c;
    --white: #ffffff;
  }
  * { margin: 0; padding: 0; box-sizing: border-box; }
  html, body {
    width: 1200px; height: 750px; overflow: hidden;
    background: var(--stage);
    font-family: "Montserrat", Arial, sans-serif;
  }
  .canvas { position: relative; width: 1200px; height: 750px; }

  /* ---------- Top panel ---------- */
  .box-top {
    position: absolute; left: 200px; top: 70px; width: 940px; height: 130px;
    overflow: hidden;
    background: linear-gradient(100deg, var(--red-deep), var(--red) 60%, var(--red-deep));
  }
  .box-top__band {
    position: absolute; left: 430px; top: 0; right: 0; bottom: 0;
    background: var(--black);
    clip-path: polygon(12% 0, 100% 0, 100% 100%, 0 100%);
  }
  .box-top__brand {
    position: absolute; left: 120px; top: 0; height: 100%;
    display: flex; align-items: center; gap: 12px;
  }
  .box-top__dot { width: 18px; height: 18px; border-radius: 50%; background: var(--white); }
  .box-top__name { color: var(--white); font-weight: 800; font-size: 28px; letter-spacing: 1.5px; }
  .box-top__type {
    position: absolute; left: 560px; top: 0; height: 100%;
    display: flex; flex-direction: column; justify-content: center;
    color: var(--white); font-weight: 700; line-height: 1.25;
  }
  .box-top__type-name { font-size: 15px; letter-spacing: 0.5px; }
  .box-top__type-code { font-size: 13px; }

  /* ---------- Side panel ---------- */
  .box-side {
    position: absolute; left: 60px; top: 200px; width: 140px; height: 460px;
    background: linear-gradient(180deg, var(--black), var(--black-soft));
  }
  .box-side__face {
    position: absolute; left: 0; top: 0; width: 100%; height: 300px;
    background: var(--side-white);
    display: flex; align-items: center; justify-content: center;
  }
  .box-side__emblem {
    width: 96px; height: 170px; border-radius: 8px;
    background: var(--side-emblem);
  }
  .box-side__spec {
    position: absolute; left: 14px; right: 10px; top: 330px;
    color: var(--white); font-weight: 700; line-height: 1.3;
  }
  .box-side__caliber { display: block; font-size: 20px; font-weight: 800; margin-bottom: 4px; }
  .box-side__line { display: block; font-size: 10px; }

  /* ---------- Front panel ---------- */
  .box-front {
    position: absolute; left: 200px; top: 200px;
    width: 940px; height: 460px; overflow: hidden;
    background: linear-gradient(115deg, var(--red-deep) 0%, var(--red) 45%, var(--red-bright) 70%, var(--red-deep) 100%);
  }
  .front-emblem {
    position: absolute; left: 40px; top: 105px; width: 330px; height: 330px;
    border-radius: 12px;
    background: radial-gradient(circle at 50% 45%, var(--emblem-tint), rgba(190, 60, 40, 0.08) 70%, transparent);
  }
  .count-band {
    position: absolute; left: 0; top: 0; width: 100%; height: 70px;
    background: linear-gradient(180deg, var(--black-soft), var(--black));
    display: flex; align-items: center; justify-content: center;
  }
  .count-band__text { color: var(--white); font-weight: 700; font-size: 24px; letter-spacing: 10px; }

  .brand {
    position: absolute; left: 160px; right: 0; top: 86px;
    display: flex; align-items: center; justify-content: center; gap: 14px;
  }
  .brand__dot { width: 24px; height: 24px; border-radius: 50%; background: var(--white); }
  .brand__name { color: var(--white); font-weight: 800; font-size: 36px; letter-spacing: 2px; }

  .headline {
    position: absolute; left: 160px; right: 0; top: 142px; text-align: center;
    font-weight: 900; line-height: 0.95; text-transform: uppercase;
    background: linear-gradient(180deg, var(--gold-light), var(--gold) 55%, var(--gold-dark));
    -webkit-background-clip: text; background-clip: text; color: transparent;
  }
  .headline__line { display: block; font-size: 48px; }
  .headline__line--wide { font-size: 56px; }
  .headline__sub {
    position: absolute; left: 160px; right: 0; top: 306px; text-align: center;
    color: var(--gold); font-weight: 700; font-size: 17px; letter-spacing: 1.5px;
  }

  .spec-band {
    position: absolute; left: 60px; right: 30px; bottom: 20px; height: 90px;
    background: var(--black);
    clip-path: polygon(0 0, 100% 0, 97% 100%, 2% 100%);
    display: flex; align-items: center; padding: 0 60px 0 90px; gap: 26px;
  }
  .spec-band__cartridge { width: 26px; height: 66px; flex: none; }
  .caliber { color: var(--gold-light); font-weight: 800; line-height: 0.9; }
  .caliber__size { display: block; font-size: 42px; }
  .caliber__weight { display: block; font-size: 24px; }
  .spec-band__divider { width: 2px; height: 60px; background: var(--gold-dark); flex: none; }
  .bullet-type { color: var(--gold); }
  .bullet-type__name { display: block; font-weight: 800; font-size: 28px; letter-spacing: 0.5px; }
  .bullet-type__code { display: block; font-weight: 700; font-size: 15px; }
</style>
</head>
<body>
<div class="canvas">

  <section class="box-top">
    <div class="box-top__band"></div>
    <div class="box-top__brand">
      <span class="box-top__dot"></span>
      <span class="box-top__name">IRON CREST ARMORY</span>
    </div>
    <div class="box-top__type">
      <span class="box-top__type-name">FULL METAL JACKET</span>
      <span class="box-top__type-code">FMJ / ELITE AMMUNITION</span>
    </div>
  </section>

  <section class="box-side">
    <div class="box-side__face">
      <div class="box-side__emblem" role="img" aria-label="Brand emblem in dark red"></div>
    </div>
    <div class="box-side__spec">
      <span class="box-side__caliber">9mm 115gr</span>
      <span class="box-side__line">FULL METAL JACKET</span>
      <span class="box-side__line">FMJ / ELITE AMMUNITION</span>
    </div>
  </section>

  <section class="box-front">
    <div class="front-emblem" role="img" aria-label="Large faint brand emblem in the background"></div>

    <header class="count-band">
      <span class="count-band__text">50 CARTRIDGES PER BOX</span>
    </header>

    <div class="brand">
      <span class="brand__dot"></span>
      <span class="brand__name">IRON CREST ARMORY</span>
    </div>

    <h1 class="headline">
      <span class="headline__line">Elite</span>
      <span class="headline__line headline__line--wide">Performance</span>
      <span class="headline__line headline__line--wide">Ammunition</span>
    </h1>
    <p class="headline__sub">CENTERFIRE CARTRIDGES</p>

    <div class="spec-band">
      <svg class="spec-band__cartridge" viewBox="0 0 26 66" role="img" aria-label="Illustration of a brass 9mm cartridge">
        <defs>
          <linearGradient id="brass" x1="0" x2="1">
            <stop offset="0" stop-color="#8a6a22"/>
            <stop offset="0.45" stop-color="#f2d27a"/>
            <stop offset="1" stop-color="#9a7428"/>
          </linearGradient>
        </defs>
        <rect x="0" y="0" width="26" height="66" rx="8" fill="url(#brass)"/>
      </svg>
      <div class="caliber">
        <span class="caliber__size">9mm</span>
        <span class="caliber__weight">115gr</span>
      </div>
      <span class="spec-band__divider"></span>
      <div class="bullet-type">
        <span class="bullet-type__name">FULL METAL JACKET</span>
        <span class="bullet-type__code">FMJ / ELITE AMMUNITION</span>
      </div>
    </div>
  </section>

</div>
</body>
</html>
```